Open Harbor book needs a cover design

I need a front and back cover design that demonstrates a strong sense of possibility that trust can be repaired even if things look bleak. Repairing trust is difficult, but this book is full of wisdom, proven strategies, and doctoral research to help people strengthen relationships and improve trust. It can help any group: business, nonprofit, education, service. Showing diversity of groups and people is very important. For the cover title, there should be a play on words: "Open Harbor: Is it? Within Reach" should have the words "is it?" crossed out and the words "It IS! should be replaced there in a striking way. Perhaps in red ink. For publishing purposes, book will be titled Open Harbor: It IS Within Reach! Please see the attachment for an example. The book layout is approximately 260 pages.

A business self-help book, but the target is any person in a group that feels they have lost trust in each other. It can be just a normal person struggling in a volunteer group they are a part of, or a supervisor whose group is not working well together. It can be a leader who just wants their group to be stronger.

Business Management

• Allise - I believe is being used on the interior of the book for the title page and headings

• Show hope and possibility in the midst of difficulty. Must have a play on the words in the title "Open Harbor: Is it? Within Reach" with crossing out "is it?" with "It IS!" (see attached example) Must include the author's name: Marla Quentin, PhD Must include a smaller tagline: "Practical Steps to Move Teams Forward Again"
• Showing diverse people, or hands. Diverse kinds of groups - not just business. A colorful cover. Maybe show the complexity of trust when it is broken...broken pieces of trust that are then picked up and put together when people work together. Could show people (or images of hands) or other ways to show that it's a choice and it is possible to repair broken trust. I'd also like to convey a sense of a group - not just random people. That they have something at stake to work on repairing trust together and this book can help them.
• If images of people are used, just showing one gender or race is not okay. Nor just binary choices: like an image containing one man and one woman, or one white person and one person of color - otherwise it seems that the book on Open Harbor is about race or gender relations.

```html
<!DOCTYPE html>
<html lang="en">
<head>
<meta charset="utf-8">
<title>Open Harbor – Book Cover</title>
<link rel="stylesheet" href="https://fonts.googleapis.com/css2?family=Source+Serif+4:opsz,wght@8..60,400;8..60,600;8..60,700;8..60,800&display=swap">
<style>
  :root {
    --backdrop: #d3e9f6;
    --paper: #ffffff;
    --ink: #111111;
    --accent-red: #e01818;
    --skin-light: #f3d6b0;
    --skin-mid: #eea07a;
    --skin-warm: #e9714a;
    --skin-deep: #d85a38;
  }
  * { margin: 0; padding: 0; box-sizing: border-box; }
  html, body {
    width: 1200px; height: 1200px; overflow: hidden;
    background: var(--backdrop);
  }
  .stage { position: relative; width: 1200px; height: 1200px; }
  .cover {
    position: absolute; left: 232px; top: 48px;
    width: 738px; height: 1107px;
    background: var(--paper);
    overflow: hidden;
    font-family: "Source Serif 4", Georgia, serif;
    color: var(--ink);
    text-align: center;
  }
  .title-line {
    position: absolute; left: 0; right: 0;
    line-height: 1; white-space: nowrap;
  }
  .title-open {
    top: 78px; left: 40px;
    font-size: 118px; font-weight: 800; letter-spacing: -1px;
  }
  .title-harbor {
    top: 168px; font-size: 150px; font-weight: 600;
    color: var(--accent-red); letter-spacing: -2px;
  }
  .title-struck {
    top: 320px; font-size: 46px; font-weight: 400; left: -10px;
  }
  .title-struck span {
    position: relative; display: inline-block; padding: 0 6px;
  }
  .title-struck span::after {
    content: ""; position: absolute; left: -24px; right: -22px; top: 54%;
    height: 3px; background: var(--accent-red);
  }
  .title-reach {
    top: 378px; font-size: 60px; font-weight: 400; left: -4px;
  }
  .tagline {
    position: absolute; left: 0; right: 0; top: 500px;
    font-size: 25px; line-height: 24px; font-weight: 400;
  }
  .author {
    position: absolute; left: 0; right: 0; top: 608px;
    font-size: 38px; line-height: 1;
  }
  .author-name { font-weight: 700; }
  .author-degree { font-weight: 400; }
  .hands-photo {
    position: absolute; left: 0; right: 0; top: 660px; bottom: 0;
    background:
      linear-gradient(180deg, var(--paper) 0%, rgba(255,255,255,0.85) 14%, rgba(255,255,255,0) 42%),
      radial-gradient(ellipse 60% 40% at 52% 18%, rgba(238,160,122,0.9), rgba(238,160,122,0) 70%),
      linear-gradient(90deg, var(--skin-light) 0%, var(--skin-mid) 40%, var(--skin-warm) 70%, var(--skin-deep) 100%);
    -webkit-mask-image: radial-gradient(ellipse 85% 110% at 52% 100%, #000 55%, transparent 100%);
            mask-image: radial-gradient(ellipse 85% 110% at 52% 100%, #000 55%, transparent 100%);
  }
</style>
</head>
<body>
  <div class="stage">
    <section class="cover" aria-label="Book cover: Open Harbor">
      <h1 class="title">
        <span class="title-line title-open">Open</span>
        <span class="title-line title-harbor">Harbor</span>
        <span class="title-line title-struck"><span>Is it?</span></span>
        <span class="title-line title-reach">Within Reach</span>
      </h1>
      <p class="tagline">Practical Steps<br>to Move Teams Forward Again</p>
      <p class="author"><span class="author-name">Marla Quentin,</span> <span class="author-degree">PhD</span></p>
      <div class="hands-photo" role="img" aria-label="Photo of many diverse arms reaching up and stacking their hands together in the centre"></div>
    </section>
  </div>
</body>
</html>
```